​Silver Harbor Rhythm provides personal, friendly service in a fun and high energy environment. We are based in Vermont.

We would like a card that appeals to a wide range of audiences as we do a wide range of events. Please feel free to check out our website silverharborrhythm.net for inspiration.

Target Market(s)

weddings, corporate, birthday parties, colleges

Industry/Entity Type

Business

Contact Information for Business Card

Silver Harbor Rhythm
Providing Entertainment For All Occasions
555 274 9160
silverharborrhythm@mailnest.net
silverharborrhythm.net

```html
<!DOCTYPE html>
<html lang="en">
<head>
<meta charset="utf-8">
<title>Silver Harbor Rhythm – Business Card</title>
<link rel="stylesheet" href="https://fonts.googleapis.com/css2?family=Open+Sans:wght@400;600;700&display=swap">
<style>
  :root {
    --backdrop: #e9e5df;
    --card-white: #ffffff;
    --brand-green: #2f6a1c;
    --ink: #111111;
    --card-dark: #1b0a0c;
    --text-light: #ffffff;
    --shadow: rgba(0, 0, 0, 0.22);
  }
  * { margin: 0; padding: 0; box-sizing: border-box; }
  html, body {
    width: 1200px;
    height: 829px;
    overflow: hidden;
    background: var(--backdrop);
    font-family: "Open Sans", Arial, sans-serif;
  }
  .stage {
    width: 1200px;
    height: 829px;
    display: flex;
    align-items: center;
    justify-content: center;
    gap: 40px;
  }
  .card {
    position: relative;
    width: 540px;
    height: 309px;
    overflow: hidden;
    box-shadow: 0 10px 24px var(--shadow);
  }
  .card-front { background: var(--card-white); }
  .card-back { background: var(--card-dark); }

  .swoosh { position: absolute; inset: 0; width: 100%; height: 100%; }

  .brand {
    position: absolute;
    left: 28px;
    top: 112px;
    display: flex;
    align-items: center;
    gap: 9px;
    color: var(--brand-green);
  }
  .brand-mark {
    width: 13px;
    height: 13px;
    background: var(--brand-green);
  }
  .brand-name {
    font-weight: 700;
    font-size: 19px;
    letter-spacing: 0.3px;
    text-transform: uppercase;
    line-height: 1;
  }

  .person {
    position: absolute;
    right: 20px;
    top: 12px;
    text-align: right;
    line-height: 1.3;
  }
  .person-name {
    color: var(--brand-green);
    font-weight: 700;
    font-size: 13px;
  }
  .person-title {
    color: var(--ink);
    font-size: 10px;
  }

  .contact {
    position: absolute;
    right: 20px;
    top: 140px;
    list-style: none;
    text-align: right;
    color: var(--text-light);
    font-size: 10.5px;
    line-height: 1.75;
  }
  .contact li { display: flex; align-items: center; justify-content: flex-end; gap: 6px; }
  .contact svg { width: 10px; height: 10px; fill: var(--text-light); }
  .contact .address { margin-top: 10px; font-size: 11px; }

  .back-content {
    position: absolute;
    inset: 0;
    display: flex;
    flex-direction: column;
    align-items: center;
    justify-content: center;
    gap: 26px;
    color: var(--text-light);
  }
  .back-brand {
    display: flex;
    align-items: center;
    gap: 14px;
  }
  .back-brand .brand-mark {
    width: 22px;
    height: 22px;
    background: var(--text-light);
  }
  .back-brand-name {
    font-weight: 700;
    font-size: 32px;
    letter-spacing: 1px;
    text-transform: uppercase;
  }
  .back-url {
    font-size: 17px;
    letter-spacing: 1.5px;
  }
</style>
</head>
<body>
<main class="stage">

  <section class="card card-front" aria-label="Business card front">
    <svg class="swoosh" viewBox="0 0 540 309" preserveAspectRatio="none" aria-hidden="true">
      <path d="M0,250 C200,290 300,200 360,140 C420,85 470,70 540,62 L540,309 L0,309 Z" fill="var(--brand-green)"/>
      <path d="M0,237 C200,277 300,187 360,127 C420,72 470,57 540,49" fill="none" stroke="var(--ink)" stroke-width="7"/>
      <path d="M0,270 C200,302 300,218 372,158" fill="none" stroke="var(--card-white)" stroke-width="1.5" opacity="0.7"/>
    </svg>

    <div class="brand">
      <span class="brand-mark"></span>
      <span class="brand-name">Silver Harbor Rhythm</span>
    </div>

    <div class="person">
      <p class="person-name">Your Name</p>
      <p class="person-title">Title</p>
    </div>

    <ul class="contact">
      <li>
        <svg viewBox="0 0 24 24" aria-hidden="true"><path d="M6.6 10.8a15 15 0 0 0 6.6 6.6l2.2-2.2a1 1 0 0 1 1-.25 11.4 11.4 0 0 0 3.6.57 1 1 0 0 1 1 1V20a1 1 0 0 1-1 1A17 17 0 0 1 3 4a1 1 0 0 1 1-1h3.5a1 1 0 0 1 1 1c0 1.25.2 2.45.57 3.57a1 1 0 0 1-.25 1z"/></svg>
        555 274 9160
      </li>
      <li>
        <svg viewBox="0 0 24 24" aria-hidden="true"><circle cx="12" cy="12" r="10"/></svg>
        www.silverharborrhythm.net
      </li>
      <li>
        <svg viewBox="0 0 24 24" aria-hidden="true"><path d="M2 5h20v14H2z"/></svg>
        silverharborrhythm@mailnest.net
      </li>
      <li class="address">Sreet Name, City Name, Zip Code:00000</li>
    </ul>
  </section>

  <section class="card card-back" aria-label="Business card back">
    <div class="back-content">
      <div class="back-brand">
        <span class="brand-mark"></span>
        <span class="back-brand-name">Silver Harbor Rhythm</span>
      </div>
      <p class="back-url">www.silverharborrhythm.net</p>
    </div>
  </section>

</main>
</body>
</html>
```